Vantrel System Web Page Design

This project is to design 6 pages of a web based medical system for clinics, hospitals, drugs suppliers, general items suppliers, insurance company, laboratories and patients (basically all parties which could be involved in).We want the designs of the browser, button, icon and layout are based on Zeltor, which is user friendly, looks professional, simple and neat but with powerful functions. We have uploaded few pictures of another system, please do not copy its design because this is not what we are looking for, the pictures are for you to know the elements should be included in our pages. Vantrel web-base system, design 6 pages1. Login PageShould include the following elements-company id with input field-login id with input field-password with input field2. Main Page (Navigation page)Should include the following elements-Appointment-Consultation-Patient-Drugs inventory -General supplies inventory -Laboratory-Suppliers-Insurance-Reports 3. Appointment PageShould include all the the elements in the respective pictures plus the followings-Daily View, Weekly View, Monthly View buttons4. Consultation PageShould include all the the elements in the respective picture5. Patient Page5.1 General information Should include all the the elements in the respective picture5.2 medical history/lab reportsShould include all the the elements in the respective picture plus the followings-Notify patient button-Share report button.
Updated on 28 Nov:
Please stop using Vantrel in your designs which is not the name of our system. We have just rename our system to Vantrel, please take note.
We need the system to look professional not playful, do not use too many colors and playful icons.

```html
<!DOCTYPE html>
<html lang="en">
<head>
<meta charset="utf-8">
<title>Vantrel – Clinic System Screens</title>
<link href="https://fonts.googleapis.com/css2?family=Lato:wght@400;700;900&display=swap" rel="stylesheet">
<style>
:root{
  --stage:#6a6a6a;
  --frame:#dcdcdc;
  --panel:#ffffff;
  --navy:#2b1fa6;
  --navy-dark:#22188a;
  --label:#3a32b0;
  --red:#b3111d;
  --ring:#dcd8f0;
  --line:#c9c9d6;
  --muted:#9a9ab0;
  --text:#333344;
}
*{box-sizing:border-box;margin:0;padding:0}
html,body{width:1200px;height:2423px;overflow:hidden}
body{background:var(--stage);font-family:'Lato',sans-serif;position:relative;color:var(--text)}
.abs{position:absolute}
.frame{position:absolute;left:128px;width:925px;background:var(--frame)}
.sheet{position:absolute;left:43px;width:851px;background:var(--panel)}

/* Screen 1: main menu */
.menu-frame{top:66px;height:722px}
.menu-sheet{top:37px;height:633px}
.date{left:41px;top:20px;font-size:14px;color:var(--label)}
.brand{left:0;right:0;top:22px;text-align:center;font-size:30px;font-weight:900;color:var(--navy);letter-spacing:.5px}
.brand-dot{display:inline-block;width:14px;height:14px;border-radius:50%;background:var(--red);margin-left:8px;vertical-align:middle}
.btn-lang{left:636px;top:26px;width:93px;height:29px;border:1.5px solid #a9a6d6;color:var(--label);font-size:13px;display:flex;align-items:center;justify-content:center}
.btn-exit{left:737px;top:26px;width:91px;height:29px;background:var(--red);color:#fff;font-size:13px;font-weight:700;display:flex;align-items:center;justify-content:center}
.tile{position:absolute;width:142px;height:142px;border-radius:50%;background:var(--ring);display:flex;align-items:center;justify-content:center}
.tile-inner{width:128px;height:128px;border-radius:50%;background:#fff;border:2px solid var(--navy);display:flex;flex-direction:column;align-items:center;justify-content:center;gap:6px}
.tile-inner svg{width:40px;height:40px;stroke:var(--red);fill:none;stroke-width:2;stroke-linecap:round;stroke-linejoin:round}
.tile-label{font-size:11.5px;font-weight:700;color:var(--navy);text-align:center;line-height:1.15;text-transform:uppercase}
.support{left:246px;top:541px;width:347px;height:47px;border-radius:24px;background:var(--red);color:#fff;display:flex;align-items:center;justify-content:center;gap:8px;font-size:17px}
.support strong{font-size:21px;font-weight:700}
.support svg{width:16px;height:16px;fill:#fff}
.copyright{left:0;right:0;top:687px;text-align:center;font-size:11px;color:#666}

/* Screen 2: patient record */
.patient-frame{top:835px;height:722px}
.patient-sheet{top:39px;height:657px}
.tabbar{left:0;top:0;width:851px;height:35px;background:var(--navy);display:flex;overflow:hidden}
.tab{flex:none;color:#fff;font-size:10px;font-weight:700;display:flex;align-items:center;justify-content:center;border-right:1px solid #5a50c0;white-space:nowrap;padding:0 2px}
.tab:last-child{border-right:0}
.field-label{position:absolute;font-size:10.5px;color:var(--label);text-align:right;width:140px}
.input{position:absolute;height:20px;border:1px solid var(--line);font-size:10px;color:#999;padding:3px 6px}
.select::after{content:"";position:absolute;right:7px;top:5px;width:6px;height:6px;border-right:1.2px solid #777;border-bottom:1.2px solid #777;transform:rotate(45deg)}
.stats{left:456px;top:58px;font-size:10px;font-weight:700;color:var(--red);white-space:nowrap}
.stats span{margin-right:14px}
.gender{left:533px;top:96px;font-size:10px;color:var(--label);display:flex;align-items:center;gap:5px}
.radio{width:9px;height:9px;border-radius:50%;border:1px solid #777;display:inline-block;position:relative}
.radio.on::after{content:"";position:absolute;left:1.5px;top:1.5px;width:4px;height:4px;border-radius:50%;background:var(--navy)}
.group-table{left:533px;top:418px;width:301px;border:1px solid var(--line)}
.group-table div{height:18px;border-bottom:1px solid var(--line)}
.group-table div:last-child{border-bottom:0}
.group-ctrl{left:790px;top:400px;display:flex;gap:3px}
.group-ctrl i{width:8px;height:8px;border-radius:50%;display:block}
.btn-outline{position:absolute;height:28px;border:1.5px solid var(--navy);color:var(--navy);font-size:12px;font-weight:700;display:flex;align-items:center;justify-content:center;background:#fff}

/* Screen 3: documents */
.docs-frame{top:1592px;height:721px}
.docs-tab{left:43px;top:41px;width:94px;height:34px;background:var(--navy);color:#fff;font-size:15px;display:flex;align-items:center;justify-content:center}
.docs-sheet{top:75px;height:541px}
.doc-card{position:absolute;width:152px;height:182px;border:1px solid #e6e6ee;background:#fff}
.doc-thumb{width:150px;height:129px}
.doc-name{position:absolute;left:12px;top:144px;font-size:10.5px;color:var(--navy);white-space:nowrap}
.doc-date{position:absolute;left:12px;top:164px;font-size:10px;color:#333}
.doc-card.alert .doc-name,.doc-card.alert .doc-date{color:var(--red)}
.doc-check{position:absolute;right:12px;top:163px;width:13px;height:13px;border:1px solid #999}
.btn-doc{position:absolute;width:128px;height:28px;border:1.5px solid var(--navy);color:var(--navy);font-size:12px;font-weight:700;display:flex;align-items:center;justify-content:center;background:#fff}
.btn-doc.faded{border-color:#b9b9c9;color:#a2a2b6;font-weight:400}
.btn-fill{position:absolute;width:128px;height:28px;color:#fff;font-size:12px;font-weight:700;display:flex;align-items:center;justify-content:center}
.fill-red{background:var(--red)}
.fill-navy{background:var(--navy)}
.btn-ghost{position:absolute;width:128px;height:28px;border:1.5px solid #b5b5c6;color:#9a9ab2;font-size:12px;display:flex;align-items:center;justify-content:center;background:var(--frame)}
.scan-slot{left:43px;top:632px;width:65px;height:50px;background:#000}
</style>
</head>
<body>

<!-- Screen 1: main navigation -->
<section class="frame menu-frame">
  <div class="sheet menu-sheet">
    <div class="abs date">Mon, 28 Jun, 2010</div>
    <div class="abs brand">Vantrel<span class="brand-dot"></span></div>
    <div class="abs btn-lang">English</div>
    <div class="abs btn-exit">Exit</div>

    <div class="tile" style="left:45px;top:148px"><div class="tile-inner">
      <svg viewBox="0 0 40 40"><rect x="6" y="9" width="28" height="25" rx="2"/><line x1="6" y1="16" x2="34" y2="16"/><line x1="13" y1="5" x2="13" y2="12"/><line x1="27" y1="5" x2="27" y2="12"/><rect x="11" y="21" width="4" height="3"/><rect x="18" y="21" width="4" height="3"/><rect x="25" y="21" width="4" height="3"/><rect x="11" y="27" width="4" height="3"/><rect x="18" y="27" width="4" height="3"/></svg>
      <div class="tile-label">Appointment</div></div></div>
    <div class="tile" style="left:202px;top:148px"><div class="tile-inner">
      <svg viewBox="0 0 40 40"><path d="M5 8h22v15H14l-5 5v-5H5z"/><path d="M27 14h8v15h-4v5l-5-5h-9v-6"/><line x1="10" y1="14" x2="22" y2="14"/><line x1="10" y1="18" x2="19" y2="18"/></svg>
      <div class="tile-label">Consultation</div></div></div>
    <div class="tile" style="left:359px;top:148px"><div class="tile-inner">
      <svg viewBox="0 0 40 40"><circle cx="20" cy="12" r="6"/><path d="M8 35c0-8 5-13 12-13s12 5 12 13z"/><line x1="20" y1="24" x2="20" y2="32"/><line x1="16" y1="28" x2="24" y2="28"/></svg>
      <div class="tile-label">Patient</div></div></div>
    <div class="tile" style="left:515px;top:148px"><div class="tile-inner">
      <svg viewBox="0 0 40 40"><rect x="9" y="5" width="14" height="5"/><rect x="7" y="10" width="18" height="24" rx="2"/><line x1="16" y1="17" x2="16" y2="25"/><line x1="12" y1="21" x2="20" y2="21"/><rect x="24" y="22" width="12" height="7" rx="3.5" transform="rotate(-30 30 25)"/></svg>
      <div class="tile-label">Drugs<br>Inventory</div></div></div>
    <div class="tile" style="left:672px;top:148px"><div class="tile-inner">
      <svg viewBox="0 0 40 40"><path d="M20 4l8 4v9l-8 4-8-4V8z"/><path d="M12 17l8 4v9l-8 4-8-4v-9z"/><path d="M28 17l8 4v9l-8 4-8-4v-9z"/></svg>
      <div class="tile-label">General Supplies<br>Inventory</div></div></div>

    <div class="tile" style="left:113px;top:314px"><div class="tile-inner">
      <svg viewBox="0 0 40 40"><path d="M10 5v12L4 32h14L12 17V5"/><line x1="8" y1="5" x2="14" y2="5"/><rect x="22" y="10" width="7" height="24" rx="3"/><rect x="30" y="16" width="6" height="18" rx="3"/><line x1="7" y1="25" x2="15" y2="25"/></svg>
      <div class="tile-label">Laboratory</div></div></div>
    <div class="tile" style="left:270px;top:314px"><div class="tile-inner">
      <svg viewBox="0 0 40 40"><circle cx="12" cy="10" r="4"/><circle cx="28" cy="10" r="4"/><circle cx="20" cy="14" r="4"/><path d="M5 28v-8c0-3 3-5 7-5"/><path d="M35 28v-8c0-3-3-5-7-5"/><path d="M13 35v-9c0-4 3-6 7-6s7 2 7 6v9"/></svg>
      <div class="tile-label">Suppliers</div></div></div>
    <div class="tile" style="left:427px;top:314px"><div class="tile-inner">
      <svg viewBox="0 0 40 40"><path d="M4 20C4 11 11 5 20 5s16 6 16 15c-3-3-6-3-8 0-2-3-6-3-8 0-2-3-6-3-8 0-2-3-5-3-8 0z"/><path d="M20 20v11c0 3-5 3-5 0"/></svg>
      <div class="tile-label">Insurance</div></div></div>
    <div class="tile" style="left:583px;top:314px"><div class="tile-inner">
      <svg viewBox="0 0 40 40"><rect x="5" y="6" width="30" height="21" rx="1"/><line x1="20" y1="27" x2="20" y2="33"/><line x1="13" y1="34" x2="27" y2="34"/><line x1="12" y1="22" x2="12" y2="16"/><line x1="17" y1="22" x2="17" y2="12"/><line x1="22" y1="22" x2="22" y2="14"/><line x1="27" y1="22" x2="27" y2="18"/></svg>
      <div class="tile-label">Reports</div></div></div>

    <div class="abs support">
      <svg viewBox="0 0 24 24"><path d="M6.6 10.8a15 15 0 0 0 6.6 6.6l2.2-2.2a1 1 0 0 1 1-.25 11.4 11.4 0 0 0 3.6.57 1 1 0 0 1 1 1V20a1 1 0 0 1-1 1A17 17 0 0 1 3 4a1 1 0 0 1 1-1h3.5a1 1 0 0 1 1 1 11.4 11.4 0 0 0 .57 3.6 1 1 0 0 1-.25 1z"/></svg>
      Support Line <strong>(852) 2000 4417</strong>
    </div>
  </div>
  <div class="abs copyright">© 2018 Company Name&nbsp; All right reserved</div>
</section>

<!-- Screen 2: patient general information -->
<section class="frame patient-frame">
  <div class="sheet patient-sheet">
    <nav class="abs tabbar">
      <div class="tab" style="width:106px">Current Queue F2</div>
      <div class="tab" style="width:116px">Today Appointment F3</div>
      <div class="tab" style="width:88px">Appointment F4</div>
      <div class="tab" style="width:88px">Weekly View F5</div>
      <div class="tab" style="width:80px">New Paitnt F6</div>
      <div class="tab" style="width:96px">Public Holiday F7</div>
      <div class="tab" style="width:58px">Recall F8</div>
      <div class="tab" style="width:82px">Laboratory F9</div>
      <div class="tab" style="width:137px">Appointment Reminder F11</div>
    </nav>

    <!-- left column -->
    <div class="field-label" style="left:-35px;top:58px">Patient Code:</div><div class="input" style="left:116px;top:54px;width:299px">021011</div>
    <div class="field-label" style="left:-35px;top:84px">English Name:</div><div class="input" style="left:116px;top:80px;width:299px"></div>
    <div class="field-label" style="left:-35px;top:110px">Chinese Namev</div><div class="input" style="left:116px;top:106px;width:299px"></div>
    <div class="field-label" style="left:-35px;top:136px">H.K.I.D:</div><div class="input" style="left:116px;top:132px;width:299px"></div>
    <div class="field-label" style="left:-35px;top:162px">D.O.B:</div><div class="input" style="left:116px;top:158px;width:299px">DD/MM/CCYY</div>
    <div class="field-label" style="left:-35px;top:188px">Mobile No.:</div><div class="input" style="left:116px;top:184px;width:299px"></div>
    <div class="field-label" style="left:-35px;top:214px">Res. Address:</div><div class="input" style="left:116px;top:210px;width:299px;height:46px"></div>
    <div class="field-label" style="left:-35px;top:268px">Res. District:</div><div class="input select" style="left:116px;top:264px;width:299px"></div>
    <div class="field-label" style="left:-35px;top:294px">Res. Area:</div><div class="input select" style="left:116px;top:290px;width:299px"></div>
    <div class="field-label" style="left:-35px;top:320px">Occupation:</div><div class="input select" style="left:116px;top:316px;width:299px"></div>
    <div class="field-label" style="left:-35px;top:346px">Contract:</div><div class="input select" style="left:116px;top:342px;width:299px"></div>
    <div class="field-label" style="left:-35px;top:372px">Insurance No:</div><div class="input" style="left:116px;top:368px;width:299px"></div>
    <div class="field-label" style="left:-35px;top:398px">Insurance Plan:</div><div class="input" style="left:116px;top:394px;width:299px;height:46px"></div>
    <div class="field-label" style="left:-35px;top:449px">Remart:</div><div class="input" style="left:116px;top:445px;width:273px;height:46px"></div>

    <!-- right column -->
    <div class="abs stats"><span>No. of Records: 4912</span><span>Last Patient Code: 02100</span><span>Last Modify Date:</span></div>
    <div class="field-label" style="left:380px;top:99px">Gender:</div>
    <div class="abs gender"><span class="radio on"></span>Male&nbsp;&nbsp;<span class="radio"></span>Female&nbsp;&nbsp;&nbsp;&nbsp;Prefix:</div>
    <div class="input select" style="left:690px;top:93px;width:144px"></div>
    <div class="field-label" style="left:380px;top:126px">Blood Type:</div><div class="input select" style="left:533px;top:122px;width:301px"></div>
    <div class="field-label" style="left:380px;top:152px">Tel:</div><div class="input" style="left:533px;top:148px;width:301px"></div>
    <div class="field-label" style="left:380px;top:178px">Bus. Address:</div><div class="input" style="left:533px;top:176px;width:301px;height:45px"></div>
    <div class="field-label" style="left:380px;top:233px">Bus. Area:</div><div class="input select" style="left:533px;top:229px;width:301px"></div>
    <div class="field-label" style="left:380px;top:258px">Dr. in Charge:</div><div class="input select" style="left:533px;top:254px;width:301px"></div>
    <div class="field-label" style="left:380px;top:283px">Referred By:</div><div class="input select" style="left:533px;top:279px;width:301px"></div>
    <div class="field-label" style="left:380px;top:308px">E-Mail:</div><div class="input select" style="left:533px;top:304px;width:301px"></div>
    <div class="field-label" style="left:380px;top:333px">Family History:</div><div class="input" style="left:533px;top:329px;width:301px;height:49px"></div>
    <div class="field-label" style="left:380px;top:396px">Group:</div><div class="input select" style="left:533px;top:392px;width:250px"></div>
    <div class="abs group-ctrl"><i style="background:var(--red)"></i><i style="border:1px solid #999"></i></div>
    <div class="abs group-table"><div></div><div></div><div></div><div></div></div>

    <div class="btn-outline" style="left:32px;top:534px;width:128px">New</div>
    <div class="btn-outline" style="left:168px;top:534px;width:128px">Save</div>
    <div class="btn-outline" style="left:304px;top:534px;width:127px">Print Eng.</div>
    <div class="btn-outline" style="left:439px;top:534px;width:128px">Print Chi.</div>
    <div class="btn-outline" style="left:572px;top:534px;width:129px">Patient Chart X</div>
    <div class="btn-outline" style="left:708px;top:534px;width:127px">Main</div>
  </div>
</section>

<!-- Screen 3: medical history and lab reports -->
<section class="frame docs-frame">
  <div class="abs docs-tab">Others</div>
  <div class="sheet docs-sheet">
    <div class="doc-card" style="left:23px;top:29px"><div class="doc-thumb" role="img" aria-label="Paper chart recording" style="background:linear-gradient(135deg,#cfe6f6,#4d8dc4)"></div><div class="doc-name">Medical Record Printing</div><div class="doc-date">26/05/2006</div><div class="doc-check"></div></div>
    <div class="doc-card" style="left:183px;top:29px"><div class="doc-thumb" role="img" aria-label="Pulmonary CT scan" style="background:linear-gradient(135deg,#1a1a1a,#8a8a8a)"></div><div class="doc-name">Pulmonary CT</div><div class="doc-date">26/05/2006</div><div class="doc-check"></div></div>
    <div class="doc-card" style="left:344px;top:29px"><div class="doc-thumb" role="img" aria-label="Knee joint scan" style="background:linear-gradient(135deg,#0d3a80,#5aa6e6)"></div><div class="doc-name">Knee</div><div class="doc-date">26/05/2006</div><div class="doc-check"></div></div>
    <div class="doc-card" style="left:506px;top:29px"><div class="doc-thumb" role="img" aria-label="Hand X-ray" style="background:linear-gradient(135deg,#0a1a3a,#5d7fb6)"></div><div class="doc-name">X-Ray Hand</div><div class="doc-date">26/05/2006</div><div class="doc-check"></div></div>
    <div class="doc-card" style="left:666px;top:29px"><div class="doc-thumb" role="img" aria-label="Frontal skull X-ray" style="background:linear-gradient(135deg,#05121c,#6c8f9e)"></div><div class="doc-name">X-Ray Frontal</div><div class="doc-date">26/05/2006</div><div class="doc-check"></div></div>

    <div class="doc-card" style="left:23px;top:226px"><div class="doc-thumb" role="img" aria-label="Chest X-ray" style="background:linear-gradient(135deg,#07203d,#7fb2d8)"></div><div class="doc-name">X-Ray Chest</div><div class="doc-date">26/05/2006</div><div class="doc-check"></div></div>
    <div class="doc-card" style="left:183px;top:226px"><div class="doc-thumb" role="img" aria-label="ECG trace over heart scan" style="background:linear-gradient(90deg,#0f3e6e,#b51a1a)"></div><div class="doc-name">ECG</div><div class="doc-date">26/05/2006</div><div class="doc-check"></div></div>
    <div class="doc-card alert" style="left:344px;top:226px"><div class="doc-thumb" role="img" aria-label="Stethoscope on a report" style="background:linear-gradient(135deg,#e4ddd2,#8aa7a8)"></div><div class="doc-name">Patient Report</div><div class="doc-date">26/05/2006</div><div class="doc-check"></div></div>
    <div class="doc-card" style="left:506px;top:226px"><div class="doc-thumb" role="img" aria-label="Medical service dashboard" style="background:linear-gradient(135deg,#0e4a4a,#2d8a86)"></div><div class="doc-name">Presentation</div><div class="doc-date">26/05/2006</div><div class="doc-check"></div></div>
    <div class="doc-card" style="left:666px;top:226px"><div class="doc-thumb" role="img" aria-label="Clipboard with information sheet" style="background:linear-gradient(135deg,#3b2a1e,#cfd8d0)"></div><div class="doc-name">Information Sheet</div><div class="doc-date">26/05/2006</div><div class="doc-check"></div></div>

    <div class="btn-doc" style="left:26px;top:426px">Scan</div>
    <div class="btn-doc" style="left:26px;top:462px">Delete</div>
    <div class="btn-doc faded" style="left:26px;top:497px">Previous page</div>
    <div class="btn-doc" style="left:351px;top:426px">Video</div>
    <div class="btn-doc" style="left:351px;top:462px">Rename C</div>
    <div class="btn-doc faded" style="left:351px;top:497px">Next page</div>
    <div class="btn-fill fill-red" style="left:688px;top:424px">Import</div>
    <div class="btn-fill fill-navy" style="left:688px;top:459px">Export</div>
  </div>
  <div class="abs scan-slot"></div>
  <div class="btn-fill fill-navy" style="left:600px;top:629px">Share Report</div>
  <div class="btn-ghost" style="left:736px;top:629px">Compare</div>
  <div class="btn-fill fill-red" style="left:600px;top:664px">Notify patient</div>
  <div class="btn-fill fill-navy" style="left:736px;top:664px">Return</div>
</section>

</body>
</html>
```